Silvermoor Property Development Co.

We need a logo and business card design for a Hong Kong based real estate company, PLX Land. We are want the brand to reflect the owners forward thinking, creative, and trend setting projects, while also reflecting a sense of security and strength. We invest in industrial properties which we convert to co-living or co-working spaces. PLX stands for Greater Bay Area which is the region around southern China including HK, Macau, and 9 other Chinese cities...made up of approx. 68 million people. There are massive infrastructure projects including the bridge to Macau and high-speed rail to SZ and the bridge connecting SZ and Zhongshan.

Target Market(s)

Chinese and western retail investors, as well as institutional investors

Industry/Entity Type

Real Estate Development

Contact Information for Business Card

Dale Whitford
CEO
dale@plxland-example.com
M + 852 9581 4062
F + 852 3864 2217
Suite 2207, The Halvern, 41 Tremont Rd., Central, Hong Kong

Logo Text

plx land (company name) lifestyle property development (underneath)

Colors

Designer to choose colors to be used in the design.

Requirements
Must have
• Details listed above. One side should include the logo and company name...plx land in modern, hip styling with "lifestyle property development"
Nice to have
• Could be a Black card, with metallic purple "plx" and white "land"...but open great design ideas
Should not have
• boring and traditional layout

```html
<!DOCTYPE html>
<html lang="en">
<head>
<meta charset="utf-8">
<title>PLX Land — Business Card</title>
<link rel="stylesheet" href="https://fonts.googleapis.com/css2?family=Oswald:wght@400&family=Open+Sans:wght@400&display=swap">
<style>
  :root {
    --backdrop: #b9b9b9;
    --card-dark: #262324;
    --purple: #9b1aa6;
    --purple-bright: #b52cc0;
    --purple-deep: #7a0a80;
    --white: #ffffff;
    --text-light: #e9e6e9;
    --divider: #4a4647;
  }
  * { margin: 0; padding: 0; box-sizing: border-box; }
  html, body {
    width: 1200px; height: 802px; overflow: hidden;
    background: var(--backdrop);
  }
  .canvas { position: relative; width: 1200px; height: 802px; }
  .card {
    position: absolute; top: 274px; width: 443px; height: 265px;
    box-shadow: 3px 4px 8px rgba(0,0,0,0.35);
    overflow: hidden;
  }
  .card-front { left: 136px; background: var(--card-dark); }
  .card-back {
    left: 624px;
    background: radial-gradient(ellipse 60% 75% at 50% 55%, var(--purple-bright) 0%, var(--purple) 50%, var(--purple-deep) 100%);
  }
  .brand {
    position: absolute; font-family: "Open Sans", sans-serif; font-weight: 400;
    white-space: nowrap; display: flex; align-items: center; gap: 10px;
  }
  .brand-dot { display: inline-block; border-radius: 50%; }
  .card-front .brand { left: 46px; top: 110px; font-size: 32px; line-height: 44px; color: var(--purple-bright); }
  .card-front .brand-dot { width: 9px; height: 9px; background: var(--purple-bright); }
  .divider {
    position: absolute; left: 234px; top: 62px; width: 1px; height: 142px;
    background: var(--divider);
  }
  .contact { position: absolute; left: 253px; top: 58px; font-family: "Open Sans", sans-serif; color: var(--text-light); }
  .contact-name {
    font-family: "Oswald", sans-serif; font-weight: 400; font-size: 18px; line-height: 22px;
    color: var(--purple-bright); text-transform: uppercase;
  }
  .contact-title { font-size: 12.5px; line-height: 16px; margin-bottom: 6px; }
  .contact-line { display: flex; align-items: center; gap: 4px; font-size: 12.5px; line-height: 16px; }
  .contact-line svg { width: 9px; height: 9px; flex: none; }
  .contact-address { font-size: 12.5px; line-height: 16px; margin-top: 8px; }
  .card-back .brand {
    left: 0; right: 0; top: 100px; justify-content: center;
    font-size: 42px; line-height: 56px; color: var(--white);
  }
  .card-back .brand-dot { width: 11px; height: 11px; background: var(--white); }
  .tagline {
    position: absolute; left: 0; right: 0; top: 179px; text-align: center;
    font-family: "Oswald", sans-serif; font-weight: 400; font-size: 13.5px;
    color: var(--white); text-transform: uppercase;
  }
</style>
</head>
<body>
<main class="canvas">
  <section class="card card-front" aria-label="Business card front">
    <div class="brand"><span>PLX Land</span><span class="brand-dot"></span></div>
    <div class="divider"></div>
    <div class="contact">
      <div class="contact-name">Dale Whitford</div>
      <div class="contact-title">CEO</div>
      <div class="contact-line">
        <svg viewBox="0 0 10 10"><rect x="2.5" y="0.5" width="5" height="9" rx="1" fill="none" stroke="#b52cc0" stroke-width="1.2"/></svg>
        <span>+ 852 9581 4062</span>
      </div>
      <div class="contact-line">
        <svg viewBox="0 0 10 10"><rect x="2.5" y="0.5" width="5" height="3" fill="#b52cc0"/><rect x="0.5" y="3.5" width="9" height="4" fill="#b52cc0"/><rect x="2.5" y="6.5" width="5" height="3" fill="#b52cc0"/></svg>
        <span>+ 852 3864 2217</span>
      </div>
      <div class="contact-line">
        <svg viewBox="0 0 10 10"><rect x="0.5" y="2" width="9" height="6.5" fill="#b52cc0"/><path d="M0.5 2 L5 5.5 L9.5 2" fill="none" stroke="#262324" stroke-width="0.9"/></svg>
        <span>dale@plxland-example.com</span>
      </div>
      <div class="contact-address">Suite 2207, The Halvern<br>41 Tremont Rd.,<br>Central, Hong Kong</div>
    </div>
  </section>
  <section class="card card-back" aria-label="Business card back">
    <div class="brand"><span>PLX Land</span><span class="brand-dot"></span></div>
    <div class="tagline">Lifestyle Property Development</div>
  </section>
</main>
</body>
</html>
```